Private Investment Firm Needs PowerPoint Presentation Template

Design PowerPoint template, take Pinebrook-submitted rough presentation draft, and drop it into new template. See attached Project Brief file for more detail.
Updates

Some decent designs have been submitted but they seem to lack the understanding of our target markets. I am hopeful that more time and feedback will result in better results.

Target Market(s)

Private company owners and intermediaries.

Font styles to use
Serif

Colors
3176b5

Requirements
Must have
• See attached Project Brief.
Nice to have
Should not have
• No B2C fluff--this is a B2B project.

```html
<!DOCTYPE html>
<html lang="en">
<head>
<meta charset="utf-8">
<title>Pinebrook Provides Junior Capital</title>
<link rel="stylesheet" href="https://fonts.googleapis.com/css2?family=Montserrat:wght@400;600;700&family=Arimo:wght@400&family=Cinzel:wght@500&display=swap">
<style>
  :root {
    --brand-blue: #1277c2;
    --accent-blue: #3176b5;
    --corner-blue: #2c83c5;
    --navy-deep: #012047;
    --navy-mid: #045692;
    --sky: #58cbec;
    --heading-navy: #0d3a70;
    --slate: #5a5a5a;
    --green: #009a48;
    --ink: #2b2b2b;
    --row-light: #f4f4f4;
    --row-dark: #dcdcdc;
    --white: #ffffff;
  }
  * { box-sizing: border-box; margin: 0; padding: 0; }
  html, body { width: 1200px; height: 675px; overflow: hidden; }
  body {
    position: relative;
    background: linear-gradient(135deg, #fafafa 0%, #f0f0f0 55%, #f6f6f6 100%);
    font-family: "Montserrat", Arial, sans-serif;
  }
  .corner-art { position: absolute; inset: 0; width: 1200px; height: 675px; }
  .title-banner { position: absolute; left: 236px; top: 50px; width: 728px; height: 46px; }
  .title-banner svg { position: absolute; inset: 0; }
  .title-text {
    position: absolute; inset: 0; display: flex; align-items: center; justify-content: center;
    color: var(--white); font-weight: 700; font-size: 32px; letter-spacing: 0.3px;
  }
  .stack { position: absolute; left: 100px; top: 119px; width: 1000px; }
  .stack-header {
    height: 52px; background: var(--sky); color: var(--heading-navy);
    font-weight: 700; font-size: 25px; display: flex; align-items: center; justify-content: center;
    letter-spacing: 0.3px;
  }
  .tier-label { position: absolute; left: 0; width: 311px; height: 38px; display: flex; }
  .tier-label .flag { width: 48px; background: var(--green); }
  .tier-label .name {
    margin-left: 4px; flex: 1; background: var(--brand-blue); color: var(--white);
    font-weight: 700; font-size: 23px; display: flex; align-items: center; justify-content: center;
  }
  .instrument {
    position: absolute; left: 0; width: 311px; height: 38px;
    background: linear-gradient(180deg, var(--row-dark) 0%, var(--row-light) 45%, var(--row-light) 100%);
    font-family: "Arimo", Arial, sans-serif; font-size: 15px; color: var(--ink);
    display: flex; align-items: center; justify-content: center;
  }
  .panel {
    position: absolute; left: 312px; width: 688px; color: var(--white);
    display: flex; flex-direction: column; align-items: center; justify-content: center;
    text-align: center; padding: 0 24px; font-size: 16px; line-height: 18px;
  }
  .panel h3 { font-weight: 700; font-size: 16.5px; line-height: 19px; }
  .panel-senior { top: 53px; height: 230px; background: var(--navy-mid); }
  .panel-junior { top: 292px; height: 155px; background: var(--navy-deep); }
  .site {
    position: absolute; left: 82px; top: 622px; font-size: 20px; color: var(--ink);
    letter-spacing: 0.2px;
  }
  .site strong { color: var(--accent-blue); font-weight: 700; }
  .wordmark { position: absolute; left: 752px; top: 590px; display: flex; align-items: center; gap: 10px; }
  .wordmark .dot { width: 30px; height: 30px; border-radius: 50%; background: var(--accent-blue); }
  .wordmark .name {
    font-family: "Cinzel", Georgia, serif; font-weight: 500; font-size: 20px;
    color: var(--heading-navy); letter-spacing: 1.5px;
  }
  .page-number { position: absolute; left: 1088px; top: 624px; color: var(--white); font-weight: 700; font-size: 12px; }
</style>
</head>
<body>
  <svg class="corner-art" viewBox="0 0 1200 675" aria-hidden="true">
    <polygon points="0,0 150,0 0,170" fill="var(--accent-blue)"/>
    <polygon points="1200,365 1200,675 922,675" fill="var(--corner-blue)"/>
  </svg>

  <header class="title-banner">
    <svg viewBox="0 0 728 46" width="728" height="46" aria-hidden="true">
      <polygon points="18,0 53,0 35,46 0,46" fill="var(--slate)"/>
      <polygon points="64,0 687,0 664,46 41,46" fill="var(--brand-blue)"/>
      <polygon points="693,0 728,0 710,46 675,46" fill="var(--slate)"/>
    </svg>
    <h1 class="title-text">Pinebrook Provides Junior Capital</h1>
  </header>

  <section class="stack">
    <h2 class="stack-header">Balance Sheet Seniority / Capital Stack Hierarchy</h2>

    <div class="tier-label" style="top:53px"><span class="flag"></span><span class="name">Senior Debt</span></div>
    <div class="instrument" style="top:91px">Revolver</div>
    <div class="instrument" style="top:130px">Asset-Based Loan</div>
    <div class="instrument" style="top:168px">Senior Term Loan</div>
    <div class="tier-label" style="top:207px"><span class="flag"></span><span class="name">Combination</span></div>
    <div class="instrument" style="top:245px">Unitranche</div>

    <div class="tier-label" style="top:292px"><span class="flag"></span><span class="name">Junior Capital</span></div>
    <div class="instrument" style="top:330px">Subordinated Debt</div>
    <div class="instrument" style="top:369px">Preferred Stock</div>
    <div class="instrument" style="top:408px">Common Stock</div>

    <div class="panel panel-senior">
      <h3>Senior Debt Capital Providers</h3>
      <p>Paid back first, plays more of a lender than partner role, less value-added,<br>less equity dilutive, less expensive capital, but not strategically focused</p>
    </div>
    <div class="panel panel-junior">
      <h3>What Pinebrook Invests</h3>
      <p>Sits junior to all other capital (taking on more risk), plays a partner role, more value-added services provided, more expensive than senior debt, but supplies an engine for continuous improvement and growth</p>
    </div>
  </section>

  <p class="site">www.<strong>pinebrookcapital</strong>.com</p>
  <div class="wordmark"><span class="dot"></span><span class="name">PINEBROOK CAPITAL</span></div>
  <span class="page-number">3.</span>
</body>
</html>
```